Life Coaching business needs a new flyer

We are an Australian business that specialises in Life Coaching, Career Coaching, Health and Wellness Coaching, Yoga and Pilates. We need a A4 double sided flyer that is full colour and folded to DL format. I have attached a couple of designs that I like and some pictures and would like the flyer to be bright yet stylish.

Industry/Entity Type

Life Coaching

```html
<!DOCTYPE html>
<html lang="en">
<head>
<meta charset="utf-8">
<title>Clearpath Coaching – Inside Spread</title>
<link href="https://fonts.googleapis.com/css2?family=Open+Sans:wght@600;700&family=Raleway:wght@400;500&display=swap" rel="stylesheet">
<style>
  :root {
    --page-bg: #ecebe8;
    --paper: #ffffff;
    --heading-blue: #1f8fd3;
    --navy: #16325c;
    --body-text: #2b2b2b;
    --band-blue: #1e91d8;
    --band-green: #5cb33a;
    --bullet-blue: #1f8fd3;
    --white: #ffffff;
  }
  * { margin: 0; padding: 0; box-sizing: border-box; }
  html, body { width: 1200px; height: 1000px; overflow: hidden; background: var(--page-bg); }
  .spread {
    position: absolute; left: 68px; top: 45px; width: 1066px; height: 822px;
    background: var(--paper); overflow: hidden;
    box-shadow: 0 2px 10px rgba(0,0,0,.12);
    font-family: "Raleway", Arial, sans-serif; color: var(--body-text);
  }
  .photo { position: absolute; }
  .section-title {
    position: absolute; font-family: "Open Sans", Arial, sans-serif; font-weight: 600;
    font-size: 16px; line-height: 20px; color: var(--heading-blue);
  }
  .copy { position: absolute; font-size: 12px; line-height: 14px; }
  .copy p + p { margin-top: 14px; }

  /* Panel one */
  .sea-photo { left: 0; top: 0; width: 354px; height: 395px;
    background: linear-gradient(180deg, #e9f6f8 0%, #a9e0e6 25%, #4fc0cc 55%, #2aa7b4 80%, #3bb6be 100%); }
  .questions { position: absolute; left: 17px; top: 30px; width: 215px;
    font-family: "Open Sans", Arial, sans-serif; font-weight: 700; font-size: 16px; line-height: 19.5px; color: var(--navy); }
  .questions p + p { margin-top: 19px; }
  .team-photo { left: 12px; top: 395px; width: 340px; height: 185px;
    background: linear-gradient(180deg, #ffffff 0%, #f1f1f1 45%, #c9d8e6 100%); }
  .mission-title { left: 20px; top: 585px; width: 300px; }
  .mission-copy { left: 20px; top: 626px; width: 318px; }

  /* Panel two */
  .couple-photo { left: 354px; top: 183px; width: 354px; height: 215px;
    background: linear-gradient(90deg, #b9825f 0%, #d9c2a8 35%, #9fc6d6 55%, #e9a36a 85%, #dd8a4f 100%); }
  .pose-photo { left: 354px; top: 638px; width: 354px; height: 142px;
    background: linear-gradient(180deg, #1c8fd0 0%, #3aa5dc 60%, #cfe6f0 100%); }

  /* Panel three */
  .help-list { position: absolute; left: 750px; top: 105px; width: 240px; list-style: none;
    font-size: 13px; line-height: 16px; font-weight: 500; color: #111; }
  .help-list li { position: relative; padding-left: 11px; margin-bottom: 3.3px; }
  .help-list li::before { content: ""; position: absolute; left: 0; top: 5px; width: 5px; height: 5px; background: var(--bullet-blue); }
  .brand { position: absolute; left: 733px; top: 505px; display: flex; align-items: center; gap: 12px; }
  .brand-dot { width: 52px; height: 52px; border-radius: 50%; background: var(--band-green); }
  .brand-name { font-family: "Open Sans", Arial, sans-serif; font-weight: 600; font-size: 17px; line-height: 20px; color: var(--heading-blue); width: 240px; }
  .joy-photo { left: 708px; top: 583px; width: 118px; height: 180px;
    background: linear-gradient(180deg, #7fc3ee 0%, #b9dff4 50%, #d8536e 100%); }
  .smile-photo { left: 828px; top: 583px; width: 118px; height: 180px;
    background: linear-gradient(180deg, #e3e6e2 0%, #cfc6bd 45%, #e59ab6 100%); }
  .hug-photo { left: 948px; top: 583px; width: 118px; height: 180px;
    background: linear-gradient(180deg, #f2d38c 0%, #b9b06e 50%, #7da64a 100%); }

  .footer-band { position: absolute; left: 0; top: 0; width: 1066px; height: 822px; pointer-events: none; }
  .contact { position: absolute; right: 28px; top: 754px; text-align: right; color: var(--white);
    font-family: "Raleway", Arial, sans-serif; font-weight: 500; font-size: 16px; line-height: 24px; }
  .contact-line { display: flex; justify-content: flex-end; align-items: center; gap: 6px; }
</style>
</head>
<body>
<main class="spread">
  <!-- Panel one -->
  <div class="photo sea-photo" role="img" aria-label="Photo of a woman floating on a red lilo in clear turquoise tropical water"></div>
  <div class="questions">
    <p>Are you looking at making changes this year?</p>
    <p>Are you stuck in a rut or at a crossroad in your life?</p>
    <p>Are you wanting to lose weigh but can’t get motivated?</p>
    <p>Do you have ongoing problems with your career, relationships, or just life itself?</p>
    <p>Life coaching is the answer</p>
  </div>
  <div class="photo team-photo" role="img" aria-label="Photo of a cheerful group of young adults celebrating"></div>
  <h2 class="section-title mission-title">Clearpath Coaching and Meditation Centre</h2>
  <div class="copy mission-copy">
    <p>Our mission is to help you become the best possible person you can be. Mentally, physically, and spiritually.</p>
    <p>We offer highly qualified and compassionate trainers/coaches for Life Coaching, Meditation, Yoga and Pilates.<br>They will guide and motivate you every step of the way to achieve all your dreams and goals.</p>
    <p>They will make you be the best you can be</p>
  </div>

  <!-- Panel two -->
  <h2 class="section-title" style="left:372px;top:23px;">Life Coaching</h2>
  <div class="copy" style="left:372px;top:46px;width:322px;">
    <p>Your Life Coach will give you the confidence and the ability to move forward in a positive manner in all areas of your life where you crave change.</p>
    <p>Life Coaching is about breaking down the barriers preventing this change from happening, and creating the ideal environment for positive action to take place. It is a holistic approach, which looks at the present and sets goals for a totally successful future.</p>
  </div>
  <div class="photo couple-photo" role="img" aria-label="Photo of a smiling older couple sharing champagne on a boat"></div>
  <h2 class="section-title" style="left:372px;top:405px;">Career Coaching</h2>
  <div class="copy" style="left:372px;top:427px;width:322px;">
    <p>Are you at a crossroads in your career and at a loss about what to do next? Do you want your work to be in alignment with the authentic you? It can be difficult to assess career options, goals, and strategies, and have the confidence to implement changes on your own. With the right coaching support, you will gain the clarity that you need to take control and have a fulfilling and rewarding career.</p>
  </div>
  <h2 class="section-title" style="left:372px;top:551px;">Wellness Coaching</h2>
  <div class="copy" style="left:372px;top:573px;width:324px;">
    <p>Health and wellness coaches help their clients find the motivation and tools to achieve their health and wellness goals, working with the client to examine and improve the psychological framework that supports those goals.</p>
  </div>
  <div class="photo pose-photo" role="img" aria-label="Photo of a woman in white holding a yoga balance pose by the sea"></div>

  <!-- Panel three -->
  <h2 class="section-title" style="left:728px;top:23px;">Why Would I Need Help?</h2>
  <div class="copy" style="left:728px;top:47px;width:290px;">
    <p>Coaching is for anyone who wants to make lasting changes in their life. Coaching can assist with such issues as:</p>
  </div>
  <ul class="help-list">
    <li>Creating a better work- life balance</li>
    <li>Resolving relationship issues</li>
    <li>Career guidance</li>
    <li>Stress management</li>
    <li>Weight loss and fitness</li>
    <li>Motivation and goal setting</li>
    <li>Boosting your self esteem</li>
    <li>Overcoming negative emotions and thoughts</li>
    <li>Better time management</li>
  </ul>
  <h2 class="section-title" style="left:728px;top:310px;">Meditation</h2>
  <div class="copy" style="left:728px;top:333px;width:300px;">
    <p>We specialise in teaching meditation from beginners to advanced and teach a variety of techniques for stress reduction, peace of mind, stillness, and clarity.</p>
  </div>
  <h2 class="section-title" style="left:728px;top:389px;">Yoga/Pilates</h2>
  <div class="copy" style="left:728px;top:412px;width:310px;">
    <p>Your highly qualified and experienced Yoga or Pilates instructor will come to you and create a fun and varied workout based on what you enjoy and what your goals are.</p>
  </div>
  <div class="brand">
    <span class="brand-dot" aria-hidden="true"></span>
    <span class="brand-name">Clearpath Coaching and Meditation Centre</span>
  </div>
  <div class="photo joy-photo" role="img" aria-label="Photo of a joyful woman with arms raised beside a pink car"></div>
  <div class="photo smile-photo" role="img" aria-label="Photo of a smiling man in a pink shirt at home"></div>
  <div class="photo hug-photo" role="img" aria-label="Photo of a mother and daughter hugging in a sunny park"></div>

  <svg class="footer-band" viewBox="0 0 1066 822" aria-hidden="true">
    <path d="M0 778 Q540 770 1066 700 L1066 822 L0 822 Z" fill="var(--band-blue)"/>
    <path d="M0 776 Q540 768 1066 698" fill="none" stroke="var(--band-green)" stroke-width="5"/>
  </svg>
  <div class="contact">
    <div class="contact-line">
      <svg width="14" height="14" viewBox="0 0 14 14" aria-hidden="true"><circle cx="7" cy="7" r="6" fill="none" stroke="#fff" stroke-width="1.3"/><path d="M4.6 4.2c.4-.4.8-.3 1 .1l.5.9c.2.3 0 .6-.2.8-.3.2-.2.5 0 .9.4.6.8 1 1.3 1.3.3.2.6.3.8 0 .2-.2.5-.4.8-.2l.9.5c.4.2.4.6.1 1-.6.7-1.6.7-2.6.1-1.2-.7-2.2-1.7-2.8-2.8-.5-1-.5-2 .2-2.6z" fill="#fff"/></svg>
      <span>02 9000 4127</span>
    </div>
    <div>www.clearpathcoaching.com.au</div>
  </div>
</main>
</body>
</html>
```